IT Management and Consulting company wants a design

The website should transfer an innovative, forward-oriented, optimistic, and serious image to my customer. Because we work in an agile, the design should transfer this approach.

The new color should make a serious, but not boring, impression for the business visitors of top-level companies.

The main focus topics are:
* IT strategy consulting
* Digital transformation
* IT quality management

The website should be in the English language.

The website should be created for WordPress. The existing website is http://www.v-tek.com (no WordPress) is provided by servplanet.de. A WordPress sandbox system exists.

Target Market(s)

Purchasing departments, IT decision makers from companies, project recruiting companies

Industry/Entity Type

IT-Provider, Telecommunication, Automotive

Number of Pages Required

4 page

Font styles to use
Serif
Sans Serif

Requirements
Must have
• Long-pager scrolling, a detail page for each portfolio topics, contact page, page about the company
Nice to have
• Parallax animation less is more, maybe a nice Hero Video Header, interessting 3D graph, Isometric graphs will bi nice, more clean than overloaded,
Should not have
• personal recruting page like in www.v-tek.com

```html
<!DOCTYPE html>
<html lang="en">
<head>
<meta charset="utf-8">
<title>Vantek Consulting</title>
<link href="https://fonts.googleapis.com/css2?family=Roboto+Slab:wght@400;700&family=Roboto:wght@400;500;700&display=swap" rel="stylesheet">
<style>
:root{
  --gold:#b8830f;
  --gold-dark:#9a6c08;
  --gold-light:#d8a53a;
  --ink:#1e1e1e;
  --text:#6b6b6b;
  --grey-band:#7b7b80;
  --footer:#1f1f21;
  --footer-text:#bdbdbd;
  --white:#ffffff;
}
*{box-sizing:border-box;margin:0;padding:0}
html,body{width:1200px;height:5085px;overflow:hidden}
body{font-family:"Roboto",Arial,sans-serif;color:var(--text);background:var(--white);position:relative}
a{color:inherit;text-decoration:none}
section,header,footer{position:absolute;left:0;width:1200px}

/* header */
.site-header{top:0;height:91px;background:var(--white);box-shadow:0 1px 4px rgba(0,0,0,.06)}
.brand{position:absolute;left:112px;top:30px;display:flex;align-items:center;gap:10px}
.brand-dot{width:10px;height:10px;background:var(--gold)}
.brand-name{font-family:"Roboto Slab",Georgia,serif;font-size:22px;color:var(--gold)}
.main-nav{position:absolute;left:487px;top:38px;display:flex;gap:34px;font-size:14px;font-weight:500;color:var(--ink)}
.login-btn{position:absolute;left:991px;top:29px;width:96px;height:36px;border-radius:18px;background:var(--gold);color:var(--white);font-size:14px;font-weight:500;display:flex;align-items:center;justify-content:center;gap:6px}

/* hero */
.hero{top:91px;height:600px;overflow:hidden}
.hero-visual{position:absolute;inset:0;background:linear-gradient(100deg,#4a3512 0%,#7b5614 35%,#b27d16 65%,#d9a539 100%)}
.hero-copy{position:absolute;left:110px;top:200px;color:var(--white)}
.hero-copy h1{font-family:"Roboto Slab",Georgia,serif;font-weight:400;font-size:38px;margin-bottom:20px}
.hero-copy h1 b{font-weight:700}
.hero-copy p{font-size:16px;font-weight:500;line-height:28px;width:480px}
.btn{display:inline-flex;align-items:center;gap:8px;border-radius:24px;background:var(--gold);color:var(--white);font-weight:700;font-size:13px;text-transform:uppercase}
.btn-arrow{width:14px;height:14px;border-radius:50%;background:var(--white);display:inline-block;position:relative}
.btn-arrow::after{content:"";position:absolute;left:4px;top:4px;border-left:5px solid var(--gold);border-top:3px solid transparent;border-bottom:3px solid transparent}
.hero .btn{position:absolute;left:113px;top:345px;height:46px;padding:0 28px;font-size:15px;background:var(--gold-dark)}

/* about */
.about{top:784px;height:410px}
.about-photo{position:absolute;left:110px;top:0;width:490px;height:407px;background:linear-gradient(135deg,#6b5540,#b99a7a 50%,#3f352c)}
.about-copy{position:absolute;left:661px;top:24px;width:427px}
.eyebrow{display:flex;align-items:center;gap:14px;color:var(--gold);font-weight:700;font-size:17px}
.eyebrow::before{content:"";width:56px;height:2px;background:var(--gold)}
.about-copy h2{font-family:"Roboto Slab",Georgia,serif;font-size:38px;font-weight:400;color:var(--ink);margin:4px 0 18px}
.about-copy h2 b{font-weight:700}
.about-copy p{font-size:13.5px;line-height:25px;text-align:justify;margin-bottom:12px}
.about-copy .btn{height:40px;padding:0 28px;margin-top:18px}

/* section titles */
.section-title{font-family:"Roboto Slab",Georgia,serif;font-size:38px;text-align:center;color:var(--ink);font-weight:700}
.section-title span{color:var(--gold);font-weight:400}

/* services */
.services-head{top:1296px}
.services{top:1392px;height:444px;display:flex}
.service{flex:1;text-align:center;color:var(--white);padding:50px 30px 0;background:var(--grey-band)}
.service:nth-child(1){background:linear-gradient(180deg,#8a8a8e,#707074)}
.service:nth-child(2){background:var(--gold)}
.service:nth-child(3){background:linear-gradient(180deg,#8d8d91,#727276)}
.service-icon{width:80px;height:80px;border-radius:50%;margin:0 auto 18px;background:var(--gold-light);border:3px solid var(--white)}
.service:nth-child(2) .service-icon{background:var(--white);border-color:var(--gold-light)}
.service h3{font-size:18px;font-weight:700;margin-bottom:12px}
.service p{font-size:13.5px;line-height:25px;margin-bottom:12px}
.learn{display:inline-flex;align-items:center;gap:8px;font-size:14px;font-weight:700;text-decoration:underline;margin-top:4px}
.learn .btn-arrow::after{border-left-color:var(--grey-band)}
.service:nth-child(2) .learn .btn-arrow::after{border-left-color:var(--gold)}

/* portfolio */
.portfolio-head{top:1914px}
.portfolio{top:2000px;height:2130px}
.connectors{position:absolute;left:0;top:0}
.project{position:absolute;width:1200px}
.project-copy{position:absolute;width:450px}
.project-copy h3{font-family:"Roboto Slab",Georgia,serif;font-size:25px;font-weight:700;color:var(--ink);letter-spacing:.5px;margin-bottom:26px}
.project-copy p{font-size:13.5px;line-height:25.5px;text-align:justify;margin-bottom:14px}
.project-copy p strong{color:var(--gold);font-weight:700}
.project-copy p.lead{color:#4a4a4a;font-weight:500}
.project-copy .btn{height:44px;padding:0 22px;margin-top:16px}
.project-photo{position:absolute;width:414px;height:414px;border-radius:50%}
.badge{position:absolute;width:88px;height:88px;border-radius:50%;background:var(--gold);border:5px solid var(--white);box-shadow:0 2px 8px rgba(0,0,0,.2)}
.badge::after{content:"";position:absolute;inset:22px;border:2px solid var(--white);border-radius:50%}

/* contact */
.contact{top:4211px;height:501px;background:radial-gradient(circle at 50% 40%,#c38e1e,#a8760c 70%)}
.contact h2{position:absolute;top:50px;width:100%;text-align:center;font-family:"Roboto Slab",Georgia,serif;font-size:34px;font-weight:700;color:var(--white)}
.contact h2 span{font-weight:400}
.field{position:absolute;background:var(--white);border:2px solid #e9d3a3;border-radius:26px;font-size:13px;color:#9a9a9a;padding:0 28px;display:flex;align-items:center}
.field.msg{border-radius:18px;align-items:flex-start;padding-top:20px}
.submit{position:absolute;left:497px;top:349px;width:210px;height:54px;border:2px solid var(--white);border-radius:27px;color:var(--white);font-weight:700;font-size:16px;display:flex;align-items:center;justify-content:center;gap:10px}
.submit .btn-arrow::after{border-left-color:var(--gold)}

/* footer */
.site-footer{top:4712px;height:373px;background:var(--footer);color:var(--footer-text)}
.footer-brand{position:absolute;left:88px;top:92px;display:flex;align-items:center;gap:10px}
.footer-brand .brand-name{color:#e6e6e6;font-size:24px}
.footer-brand .brand-dot{background:#e6e6e6}
.socials{position:absolute;left:134px;top:175px;display:flex;gap:11px}
.socials span{width:30px;height:30px;border:1.5px solid #d0d0d0;border-radius:50%}
.footer-col{position:absolute;top:71px;font-size:13px}
.footer-col h4{color:var(--white);font-size:15px;font-weight:700;margin-bottom:20px}
.footer-col li{list-style:none;line-height:26px}
.contact-item{display:flex;gap:12px;margin-bottom:12px;line-height:19px}
.contact-item svg{flex:none;margin-top:3px}
.contact-item b{display:block;color:var(--white);font-size:11px}
.footer-rule{position:absolute;left:88px;right:88px;top:304px;height:1px;background:#3a3a3c}
.copyright{position:absolute;top:330px;width:100%;text-align:center;font-size:13px;color:#d6d6d6}
.to-top{position:absolute;left:1106px;top:286px;width:34px;height:34px;border-radius:50%;background:var(--gold)}
</style>
</head>
<body>

<header class="site-header">
  <a class="brand" href="#"><span class="brand-dot"></span><span class="brand-name">Vantek Consulting</span></a>
  <nav class="main-nav">
    <a href="#">Home</a><a href="#">About Us</a><a href="#">Our Services</a><a href="#">Portfolio</a><a href="#">Contact Us</a>
  </nav>
  <a class="login-btn" href="#">
    <svg width="11" height="13" viewBox="0 0 11 13"><rect x="0" y="5" width="11" height="8" rx="1" fill="#fff"/><path d="M2.5 5V3.5a3 3 0 0 1 6 0V5" stroke="#fff" stroke-width="1.6" fill="none"/></svg>
    Login
  </a>
</header>

<section class="hero">
  <div class="hero-visual" role="img" aria-label="Golden business background with a rising arrow over growth bar charts, a world map and financial figures"></div>
  <div class="hero-copy">
    <h1><b>Vantek</b> Consulting</h1>
    <p>Whether IT project management, consulting, commissioning management or system integration</p>
  </div>
  <a class="btn" href="#">Get Started <span class="btn-arrow"></span></a>
</section>

<section class="about">
  <div class="about-photo" role="img" aria-label="Team meeting in a bright loft office around a wooden table"></div>
  <div class="about-copy">
    <div class="eyebrow">About Us</div>
    <h2><b>Vantek</b> Consulting</h2>
    <p>Whether IT project management, consulting, commissioning management or system integration: With Vantek Consulting you create the best conditions for IT systems that do what they should. In compliance with all time and cost specifications.</p>
    <p>Well-known companies from the automotive and telecommunications industries regularly use our know-how in the form of individual management and consulting services.</p>
    <a class="btn" href="#">Learn More <span class="btn-arrow"></span></a>
  </div>
</section>

<section class="services-head"><h2 class="section-title">Our <span>Services</span></h2></section>

<section class="services">
  <article class="service">
    <div class="service-icon" role="img" aria-label="Strategy icon"></div>
    <h3>IT strategy consulting</h3>
    <p>Lorem ipsum dolor sit amet, consectetur adipiscing elit, sed do eiusmod tempor incididunt ut labore et dolore magna aliqua.</p>
    <p>Ut enim ad minim veniam, quis nostrud exercitation ullamco laboris nisi ut aliquip ex ea commodo Duis aute irure dolor in reprehenderit in</p>
    <a class="learn" href="#">LEARN MORE <span class="btn-arrow"></span></a>
  </article>
  <article class="service">
    <div class="service-icon" role="img" aria-label="Digital transformation icon"></div>
    <h3>Digital transformation</h3>
    <p>Lorem ipsum dolor sit amet, consectetur adipiscing elit, sed do eiusmod tempor incididunt ut labore et dolore magna aliqua.</p>
    <p>Ut enim ad minim veniam, quis nostrud exercitation ullamco laboris nisi ut aliquip ex ea commodo Duis aute irure dolor in reprehenderit in</p>
    <a class="learn" href="#">LEARN MORE <span class="btn-arrow"></span></a>
  </article>
  <article class="service">
    <div class="service-icon" role="img" aria-label="Quality management icon"></div>
    <h3>IT quality management</h3>
    <p>Lorem ipsum dolor sit amet, consectetur adipiscing elit, sed do eiusmod tempor incididunt ut labore et dolore magna aliqua.</p>
    <p>Ut enim ad minim veniam, quis nostrud exercitation ullamco laboris nisi ut aliquip ex ea commodo Duis aute irure dolor in reprehenderit in</p>
    <a class="learn" href="#">LEARN MORE <span class="btn-arrow"></span></a>
  </article>
</section>

<section class="portfolio-head"><h2 class="section-title">Our <span>Portfolio</span></h2></section>

<section class="portfolio">
  <svg class="connectors" width="1200" height="2130" viewBox="0 0 1200 2130" fill="none" stroke="#c9c9c9" stroke-width="1.2" stroke-dasharray="4 4">
    <path d="M880 470 V500 Q880 517 863 517 H337 Q320 517 320 534 V574"/>
    <path d="M320 990 V1033 Q320 1050 337 1050 H863 Q880 1050 880 1067 V1115"/>
    <path d="M880 1530 V1572 Q880 1589 863 1589 H337 Q320 1589 320 1606 V1648"/>
  </svg>

  <article class="project" style="top:0">
    <div class="project-copy" style="left:110px;top:60px">
      <h3>PROJECTS IN EXCELLENCE</h3>
      <p><strong>Excellent project management:</strong> Excellent project management: We manage projects according to the IPLA Competence Baseline (International Project Leadership Association), according to the agile Scrum process model, or use classic models supplemented by agile approaches in hybrid project management. You can participate in it.</p>
      <p><strong>Excellent quality:</strong> Defects recognized late are expensive. We carry out quality assurance of software in an integrated</p>
      <a class="btn" href="#">Read More <span class="btn-arrow"></span></a>
    </div>
    <div class="project-photo" style="left:675px;top:35px;background:linear-gradient(135deg,#d7dee6,#8ea0b4 55%,#3c4b5e)" role="img" aria-label="Two business people talking in a modern glass office"></div>
    <div class="badge" style="left:630px;top:200px" role="img" aria-label="Award icon"></div>
  </article>

  <article class="project" style="top:574px">
    <div class="project-photo" style="left:110px;top:0;background:linear-gradient(135deg,#e3e7ec,#9aa6b3 50%,#3b3f46)" role="img" aria-label="Presenter at a whiteboard in front of a seated team"></div>
    <div class="badge" style="left:480px;top:150px" role="img" aria-label="Team icon"></div>
    <div class="project-copy" style="left:640px;top:36px">
      <h3>CONSULTING IN EXCELLENCE</h3>
      <p class="lead">The success of any IT measure is decided long before the first line of the program. In addition to technical and specialist know-how, planning is primarily about intensive communication with future users. Early test planning helps ensure that requirements and functions match exactly.</p>
      <p>In the IT Consulting service area, Vantek Consulting determines the requirements of future users, checks them for technical feasibility and translates them into precisely defined and, if necessary,</p>
      <a class="btn" href="#">Read More <span class="btn-arrow"></span></a>
    </div>
  </article>

  <article class="project" style="top:1115px">
    <div class="project-copy" style="left:110px;top:36px">
      <h3>DIGITALIZATION</h3>
      <p><strong>Excellent project management:</strong> Excellent project management: We manage projects according to the IPLA Competence Baseline (International Project Leadership Association), according to the agile Scrum process model, or use classic models supplemented by agile approaches in hybrid project management. You can participate in it.</p>
      <p><strong>Excellent quality:</strong> Defects recognized late are expensive. We carry out quality assurance of software in an integrated</p>
      <a class="btn" href="#">Read More <span class="btn-arrow"></span></a>
    </div>
    <div class="project-photo" style="left:675px;top:0;background:linear-gradient(135deg,#f3d8dc,#8b8fb8 50%,#2a2f5a)" role="img" aria-label="Businessman working on a laptop with digital network overlay"></div>
    <div class="badge" style="left:630px;top:160px" role="img" aria-label="Digital icon"></div>
  </article>

  <article class="project" style="top:1648px">
    <div class="project-photo" style="left:110px;top:0;background:linear-gradient(135deg,#cfd3d6,#8e8a84 50%,#4a4642)" role="img" aria-label="Two colleagues reviewing documents at a laptop"></div>
    <div class="badge" style="left:480px;top:150px" role="img" aria-label="Cloud database icon"></div>
    <div class="project-copy" style="left:640px;top:36px">
      <h3>CLOUD TRANSITION</h3>
      <p>Mittelfristig wird Cloud Computing das bevorzugte IT-Architektur-Modell und technologische Framework in den meisten Unternehmen sein. Für die IT bedeutet das die Bereitstellung skalierbarer und agiler cloudbasierter Services und nativer Cloud Workloads sowie die Modernisierung der vorhandenen konventionellen Systeme und Anwendungen im Backend.</p>
      <p><strong>Business Case:</strong> Wir unterstützen Sie bei der Erstellung eines Business Cases, arbeiten die Vorteile heraus und zeigen auf,</p>
      <a class="btn" href="#">Read More <span class="btn-arrow"></span></a>
    </div>
  </article>
</section>

<section class="contact">
  <h2>Contact <span>Us</span></h2>
  <div class="field" style="left:193px;top:123px;width:394px;height:52px">Name</div>
  <div class="field" style="left:193px;top:189px;width:394px;height:52px">Email Address</div>
  <div class="field" style="left:193px;top:254px;width:394px;height:52px">Phone Number</div>
  <div class="field msg" style="left:610px;top:122px;width:397px;height:186px">Message</div>
  <a class="submit" href="#">SUBMIT NOW <span class="btn-arrow"></span></a>
</section>

<footer class="site-footer">
  <div class="footer-brand"><span class="brand-dot"></span><span class="brand-name">Vantek Consulting</span></div>
  <div class="socials" aria-label="Social media links"><span></span><span></span><span></span><span></span></div>

  <div class="footer-col" style="left:436px">
    <h4>Quick Links</h4>
    <ul><li>Home</li><li>About Us</li><li>Our Services</li><li>Portfolio</li><li>Contact Us</li></ul>
  </div>
  <div class="footer-col" style="left:618px">
    <h4>About Company</h4>
    <ul><li>Terms &amp; Conditions</li><li>Privacy Policy</li><li>Support</li><li>Site Map</li><li>FAQ</li></ul>
  </div>
  <div class="footer-col" style="left:853px">
    <h4>Contact Us</h4>
    <div class="contact-item">
      <svg width="12" height="12" viewBox="0 0 12 12"><path d="M2 1l2 0 1 3-1.5 1a6 6 0 0 0 3.5 3.5L8 7l3 1v2a1 1 0 0 1-1 1A9 9 0 0 1 1 2a1 1 0 0 1 1-1z" fill="#b8830f"/></svg>
      <div><b>Phone</b>+49 (0) 8000 5550100</div>
    </div>
    <div class="contact-item">
      <svg width="12" height="10" viewBox="0 0 12 10"><rect width="12" height="10" rx="1" fill="#b8830f"/><path d="M0 1l6 4 6-4" stroke="#1f1f21" fill="none"/></svg>
      <div><b>Email</b>info (at) vantekcons.example</div>
    </div>
    <div class="contact-item">
      <svg width="10" height="13" viewBox="0 0 10 13"><path d="M5 0a5 5 0 0 1 5 5c0 3-5 8-5 8S0 8 0 5a5 5 0 0 1 5-5z" fill="#b8830f"/><circle cx="5" cy="5" r="1.8" fill="#1f1f21"/></svg>
      <div><b>Location</b>Parkstraße 12 - 14<br>D-80000 Musterstadt</div>
    </div>
  </div>

  <div class="footer-rule"></div>
  <a class="to-top" href="#" aria-label="Back to top"><svg width="34" height="34" viewBox="0 0 34 34"><path d="M11 20l6-6 6 6" stroke="#fff" stroke-width="2.2" fill="none"/></svg></a>
  <p class="copyright">2021 Copyright - Vantek Consulting | All Rights Reserved</p>
</footer>

</body>
</html>
```